BWP Business Card

A double sided business card based on your "Brindlewood Partners Ltd" Logo. To use the "BWP" logo on 1 side and the full company logo on the reverse.

Detials to be included:

Name: Tomas Wheeler
Postion: Consultant Orthotist & Expert Witness
T: +44 (0) 7700 938271
F: +44 (0) 7654 8820

```html
<!DOCTYPE html>
<html lang="en">
<head>
<meta charset="utf-8">
<title>BWP Business Card</title>
<link rel="stylesheet" href="https://fonts.googleapis.com/css2?family=Cinzel:wght@500;600&family=Open+Sans:wght@400;700&display=swap">
<style>
  :root {
    --navy: #003a6e;
    --grey: #999999;
    --rule: #cfcfcf;
    --text: #2a2a2a;
    --paper: #ffffff;
    --stage: #e9e8ef;
  }
  * { box-sizing: border-box; margin: 0; padding: 0; }
  html, body { width: 1200px; height: 987px; overflow: hidden; }
  body {
    background: var(--stage);
    font-family: "Open Sans", Arial, sans-serif;
    display: flex;
    align-items: center;
    justify-content: center;
    gap: 40px;
  }
  .card {
    width: 530px;
    height: 340px;
    border-radius: 26px;
    position: relative;
    overflow: hidden;
  }
  .card--front { background: var(--paper); padding: 34px 36px; }
  .card--back {
    background: var(--navy);
    display: flex;
    align-items: center;
    justify-content: center;
  }

  .brand { display: flex; align-items: center; height: 108px; }
  .brand__mark { display: flex; align-items: center; gap: 10px; padding-right: 22px; }
  .brand__square { width: 30px; height: 30px; background: var(--navy); }
  .brand__initials {
    font-family: "Cinzel", Georgia, serif;
    font-weight: 600;
    font-size: 44px;
    color: var(--navy);
    letter-spacing: 4px;
  }
  .brand__divider { width: 1px; height: 90px; background: var(--rule); }
  .brand__name { padding-left: 20px; }
  .brand__title {
    font-family: "Cinzel", Georgia, serif;
    font-weight: 600;
    font-size: 22px;
    line-height: 1.05;
    color: var(--navy);
  }
  .brand__tagline {
    font-family: "Cinzel", Georgia, serif;
    font-weight: 500;
    font-size: 8.5px;
    letter-spacing: 0.4px;
    color: var(--text);
    margin-top: 5px;
    padding-bottom: 3px;
    border-bottom: 1px solid var(--grey);
    display: inline-block;
  }

  .rule { height: 1px; background: var(--rule); margin: 14px 0 12px; }

  .holder { font-size: 15px; color: var(--grey); }
  .holder__name { font-weight: 700; color: var(--navy); }

  .details { margin-top: 12px; font-size: 13px; color: var(--text); line-height: 1.75; padding-left: 22px; }
  .details__row { display: flex; align-items: center; gap: 6px; }
  .details__row--address { padding-left: 20px; }
  .icon { width: 14px; height: 14px; fill: var(--navy); flex: none; }
  .details__gap { width: 12px; }

  .rule--bottom { position: absolute; left: 36px; right: 36px; bottom: 26px; margin: 0; }

  .back-mark { display: flex; align-items: center; gap: 18px; }
  .back-mark__square { width: 46px; height: 46px; background: var(--grey); }
  .back-mark__initials {
    font-family: "Cinzel", Georgia, serif;
    font-weight: 600;
    font-size: 78px;
    letter-spacing: 10px;
    color: var(--grey);
  }
</style>
</head>
<body>
  <section class="card card--front">
    <header class="brand">
      <div class="brand__mark">
        <span class="brand__square"></span>
        <span class="brand__initials">BWP</span>
      </div>
      <span class="brand__divider"></span>
      <div class="brand__name">
        <p class="brand__title">BRINDLEWOOD<br>PARTNERS LTD</p>
        <p class="brand__tagline">CLARITY IN CLINICAL EXPERT OPINION</p>
      </div>
    </header>

    <div class="rule"></div>

    <p class="holder"><span class="holder__name">Tomas Wheeler,</span> Consultant Orthotist &amp; Expert Witness</p>

    <div class="details">
      <p class="details__row details__row--address">17 Harrow Lane Kingsmere, Surrey, KT9 4RD</p>
      <p class="details__row">
        <svg class="icon" viewBox="0 0 16 16" aria-hidden="true"><circle cx="8" cy="8" r="8"/><path d="M5 4.5l1.5-.5 1 2-1 .8c.4 1 1.2 1.8 2.2 2.2l.8-1 2 1-.5 1.5c-3 .3-6.3-3-6-6z" fill="#fff"/></svg>
        +44 (0) 7700 938271
        <span class="details__gap"></span>
        <svg class="icon" viewBox="0 0 16 16" aria-hidden="true"><rect x="4" y="1" width="8" height="14" rx="1.5"/><rect x="5.5" y="3" width="5" height="8" fill="#fff"/></svg>
        +44 (0) 7654 8820
      </p>
      <p class="details__row">
        <svg class="icon" viewBox="0 0 16 16" aria-hidden="true"><circle cx="8" cy="8" r="8"/><rect x="3.5" y="5" width="9" height="6" fill="#fff"/><path d="M3.5 5l4.5 3.5L12.5 5" fill="none" stroke="#003a6e" stroke-width="1"/></svg>
        tomas@brindlewoodpartners.co.uk
      </p>
    </div>

    <div class="rule rule--bottom"></div>
  </section>

  <section class="card card--back">
    <div class="back-mark">
      <span class="back-mark__square"></span>
      <span class="back-mark__initials">BWP</span>
    </div>
  </section>
</body>
</html>
```